Harborline Auto LLC

Car Dealer Customer Service
Address: 2874 Cresthaven Road, Shelbyville, TN 37162
web: www.harborlineautoxq.net
email: harborlineautoxq@mailnest.example
Phone: (931) 555-0148
Phone: (629) 555-0173

```html
<!DOCTYPE html>
<html lang="en">
<head>
<meta charset="utf-8">
<title>Harborline Auto – Business Card</title>
<link rel="stylesheet" href="https://fonts.googleapis.com/css2?family=Lexend:wght@700&family=Poppins:ital,wght@0,400;0,600;1,400&display=swap">
<style>
  :root {
    --backdrop: #2b2b2b;
    --blue: #1d74a8;
    --blue-light: #2487c0;
    --blue-deep: #176795;
    --gold: #d9a03c;
    --paper: #f2f2f1;
    --ink: #1c1c1c;
    --white: #ffffff;
    --disc: #eef1f3;
  }
  * { margin: 0; padding: 0; box-sizing: border-box; }
  html, body {
    width: 1200px; height: 1138px; overflow: hidden;
    background: var(--backdrop);
    font-family: "Poppins", sans-serif;
  }
  .card {
    position: absolute;
    border-radius: 16px;
    overflow: hidden;
  }
  .card-front {
    left: 274px; top: 186px; width: 623px; height: 376px;
    background: linear-gradient(160deg, var(--blue-light) 0%, var(--blue) 55%, var(--blue-deep) 100%);
  }
  .card-back {
    left: 276px; top: 608px; width: 618px; height: 374px;
    background: var(--paper);
  }
  .brand-disc {
    position: absolute; border-radius: 50%;
    background: var(--disc);
  }
  .card-front .brand-disc { left: -72px; top: 20px; width: 344px; height: 344px; }
  .card-back .brand-disc { left: 346px; top: 108px; width: 220px; height: 220px; }
  .wordmark {
    position: absolute;
    font-family: "Lexend", sans-serif; font-weight: 700;
    text-transform: uppercase; letter-spacing: 0.5px; white-space: nowrap;
    line-height: 1;
  }
  .card-front .wordmark {
    right: 41px; top: 62px; font-size: 29px; color: var(--white);
  }
  .card-front .site {
    position: absolute; right: 41px; top: 322px;
    font-size: 15px; color: var(--white);
  }
  .card-back .wordmark {
    left: 28px; top: 42px; font-size: 45px; color: var(--blue);
  }
  .band { position: absolute; left: 0; width: 100%; }
  .band-blue { top: 118px; height: 140px; background: var(--blue); }
  .band-gold { top: 258px; height: 60px; background: var(--gold); }
  .role {
    position: absolute; left: 28px; top: 143px;
    font-style: italic; font-size: 17px; color: var(--white);
  }
  .phones { position: absolute; left: 28px; top: 174px; list-style: none; }
  .phones li {
    display: flex; align-items: center; gap: 14px; height: 29px;
    font-weight: 600; font-size: 22px; letter-spacing: 1px; color: var(--white);
  }
  .phones svg { width: 19px; height: 19px; fill: var(--gold); }
  .links { position: absolute; left: 28px; top: 263px; list-style: none; }
  .links li {
    display: flex; align-items: center; gap: 12px; height: 23px;
    font-size: 14.5px; color: var(--ink);
  }
  .links svg { width: 15px; height: 15px; fill: none; stroke: var(--ink); stroke-width: 1.8; }
  .address {
    position: absolute; left: 28px; top: 330px;
    font-size: 16px; color: var(--ink);
  }
</style>
</head>
<body>
  <section class="card card-front">
    <div class="brand-disc" role="img" aria-label="Brand emblem area"></div>
    <h1 class="wordmark">Harborline Auto</h1>
    <p class="site">www.harborlineautoxq.net</p>
  </section>

  <section class="card card-back">
    <h2 class="wordmark">Harborline Auto</h2>
    <div class="band band-blue"></div>
    <div class="band band-gold"></div>
    <div class="brand-disc" role="img" aria-label="Brand emblem area"></div>
    <p class="role">Car Dealer Customer Service</p>
    <ul class="phones">
      <li><svg viewBox="0 0 24 24"><path d="M6.6 10.8a15.1 15.1 0 0 0 6.6 6.6l2.2-2.2a1 1 0 0 1 1-.25 11.4 11.4 0 0 0 3.6.57 1 1 0 0 1 1 1V20a1 1 0 0 1-1 1A17 17 0 0 1 3 4a1 1 0 0 1 1-1h3.5a1 1 0 0 1 1 1c0 1.25.2 2.45.57 3.57a1 1 0 0 1-.25 1z"/></svg>931-555-0148</li>
      <li><svg viewBox="0 0 24 24"><path d="M6.6 10.8a15.1 15.1 0 0 0 6.6 6.6l2.2-2.2a1 1 0 0 1 1-.25 11.4 11.4 0 0 0 3.6.57 1 1 0 0 1 1 1V20a1 1 0 0 1-1 1A17 17 0 0 1 3 4a1 1 0 0 1 1-1h3.5a1 1 0 0 1 1 1c0 1.25.2 2.45.57 3.57a1 1 0 0 1-.25 1z"/></svg>629-555-0173</li>
    </ul>
    <ul class="links">
      <li><svg viewBox="0 0 24 24"><circle cx="12" cy="12" r="9"/><path d="M3 12h18M12 3c3 3.2 3 14.8 0 18M12 3c-3 3.2-3 14.8 0 18"/></svg>www.harborlineautoxq.net</li>
      <li><svg viewBox="0 0 24 24"><rect x="3" y="5" width="18" height="14" rx="1"/><path d="M3 6l9 7 9-7"/></svg>harborlineautoxq@mailnest.example</li>
    </ul>
    <p class="address">2874 Cresthaven Road, Shelbyville, TN 37162</p>
  </section>
</body>
</html>
```